Halvex Power

We need a business card for "Halvex power". I have uploaded the logo, the color of the card should be according to the logo "Blackish".
Basically halvex power is a solar company.
Also we would like a sample file in which we can edit the information such names and contact details ourselves
The card would be two sided with following details
1- logo on front and underneath the logo there should be a line saying
"Cleaner . Cheaper . Power"
2-website i.e "www.halvexpowerco.com"
3- Icons for Facebook and Instagram that tells the clients we are available on both social sites.
4- name of the person with his/her designation underneath and email address
5-contact number
6- 1-800--- number with the extension number

its up to the designer how he/she places the details,but it must look professional

Industry/Entity Type

Business

Contact Information for Business Card

5-contact number

Requirements
Must have
• 1- logo on front and underneath the logo there should be a line saying
• "Cleaner . Cheaper . Power"
• 2-website i.e "www.halvexpowerco.com"
• 3- Icons for Facebook and Instagram that tells the clients we are available on both social sites.
• 4- name of the person with his/her designation underneath and email address
• 5-contact number of the person
• 6- 1-800--- number with the extension number
• 7-card should be in black shade like the logo

```html
<!DOCTYPE html>
<html lang="en">
<head>
<meta charset="utf-8">
<title>Halvex Power – Business Card</title>
<link rel="stylesheet" href="https://fonts.googleapis.com/css2?family=Source+Sans+3:wght@400;600;700&display=swap">
<style>
  :root {
    --green: #8cc63f;
    --black: #232325;
    --charcoal: #3a3a3c;
    --white: #ffffff;
    --silver: #c9cacc;
    --backdrop: #eeeeec;
    --card-shadow: 0 6px 18px rgba(0,0,0,0.18);
  }
  * { box-sizing: border-box; margin: 0; padding: 0; }
  html, body {
    width: 1200px; height: 900px; overflow: hidden;
    background: var(--backdrop);
    font-family: "Source Sans 3", "Myriad Pro", sans-serif;
  }
  .stage { position: relative; width: 1200px; height: 900px; }

  .card { position: absolute; box-shadow: var(--card-shadow); overflow: hidden; }

  /* Front */
  .card-front { left: 78px; top: 35px; width: 588px; height: 363px; background: var(--white); }
  .card-front .shapes { position: absolute; inset: 0; }
  .brand {
    position: absolute; left: 0; right: 0; top: 58px;
    display: flex; flex-direction: column; align-items: center; gap: 6px;
  }
  .brand-row { display: flex; align-items: center; gap: 12px; }
  .brand-dot { width: 18px; height: 18px; border-radius: 50%; background: var(--green); }
  .brand-name { font-weight: 700; font-size: 42px; line-height: 1; color: var(--black); letter-spacing: 0.5px; }
  .tagline {
    font-weight: 600; font-size: 14px; letter-spacing: 3px;
    text-transform: uppercase; color: var(--green);
  }

  .contact-list {
    position: absolute; left: 30px; top: 254px; list-style: none;
    color: var(--white); font-size: 15.5px; line-height: 21.5px;
  }
  .contact-list li { display: flex; align-items: center; gap: 8px; }
  .contact-list svg { width: 13px; height: 13px; flex: none; }

  .person { position: absolute; right: 35px; top: 244px; text-align: right; color: var(--white); }
  .person-name { font-weight: 700; font-size: 20px; line-height: 24px; letter-spacing: 0.6px; text-transform: uppercase; }
  .person-role { font-size: 15.5px; line-height: 20px; color: var(--green); }

  .social { position: absolute; right: 37px; top: 302px; display: flex; gap: 11px; }
  .social-tile { width: 31px; height: 31px; background: var(--green); }

  /* Back */
  .card-back {
    left: 388px; top: 505px; width: 567px; height: 352px; background: var(--black);
    display: flex; flex-direction: column; align-items: center; justify-content: center; gap: 10px;
  }
  .back-accent { position: absolute; left: 0; right: 0; bottom: 0; height: 10px; background: var(--green); }
  .back-name { font-weight: 700; font-size: 58px; line-height: 1; color: var(--silver); }
  .back-tagline { font-weight: 600; font-size: 16px; letter-spacing: 3.5px; text-transform: uppercase; color: var(--green); }
</style>
</head>
<body>
<main class="stage">

  <section class="card card-front" aria-label="Business card front">
    <svg class="shapes" viewBox="0 0 588 363" aria-hidden="true">
      <polygon points="0,188 392,188 369,214 0,214" fill="var(--green)"/>
      <polygon points="0,217 372,217 400,180 588,180 588,363 0,363" fill="var(--black)"/>
    </svg>

    <div class="brand">
      <div class="brand-row">
        <span class="brand-dot"></span>
        <span class="brand-name">Halvex Power</span>
      </div>
      <p class="tagline">Cleaner . Cheaper . Power</p>
    </div>

    <ul class="contact-list">
      <li>
        <svg viewBox="0 0 14 14"><rect x="3.5" y="0.5" width="7" height="13" rx="1.2" fill="none" stroke="#8cc63f" stroke-width="1.4"/><rect x="6" y="11" width="2" height="1.2" fill="#8cc63f"/></svg>
        044-555 010 234
      </li>
      <li>
        <svg viewBox="0 0 14 14"><path d="M1 5 Q7 0 13 5 L11 7 L9 5.5 V4.5 H5 V5.5 L3 7 Z" fill="#8cc63f"/><rect x="2.5" y="7.5" width="9" height="5" rx="1" fill="#8cc63f"/></svg>
        1-800-555-0199 Ext. 204
      </li>
      <li>
        <svg viewBox="0 0 14 14"><rect x="1" y="3" width="12" height="8.5" fill="#8cc63f"/><path d="M1 3 L7 8 L13 3" fill="none" stroke="var(--black)" stroke-width="1.2"/></svg>
        info@halvexpowerco.com
      </li>
      <li>
        <svg viewBox="0 0 14 14"><circle cx="7" cy="7" r="6" fill="#8cc63f"/><path d="M4 4 Q6 6 5 8 Q8 9 7 12 M9 2.5 Q8.5 5 11 6" fill="none" stroke="var(--black)" stroke-width="1.2"/></svg>
        www.halvexpowerco.com
      </li>
    </ul>

    <div class="person">
      <p class="person-name">Daniel Reyes</p>
      <p class="person-role">Managing Director</p>
    </div>

    <div class="social" aria-label="Social profiles">
      <span class="social-tile"></span>
      <span class="social-tile"></span>
    </div>
  </section>

  <section class="card card-back" aria-label="Business card back">
    <span class="back-name">Halvex Power</span>
    <span class="back-tagline">Cleaner . Cheaper . Power</span>
    <span class="back-accent"></span>
  </section>

</main>
</body>
</html>
```